Web App Design Project

Need to provide graphical design of 2 web pages according to attached wireframes.

Colors should be adjusted for the 65+ population meaning not too bright.

App logo should be created as well - logo should represent long and good life.

Target Market(s)

65 years old and above

```html
<!DOCTYPE html>
<html lang="en">
<head>
<meta charset="utf-8">
<title>Home Measurements</title>
<link href="https://fonts.googleapis.com/css2?family=Arimo:wght@400;700&display=swap" rel="stylesheet">
<style>
:root{
  --page:#e9eaeb;
  --header-top:#66c6f3;
  --header-bottom:#3f95d6;
  --accent:#3a96d3;
  --panel:#f3f3f4;
  --white:#ffffff;
  --ink:#4d5160;
  --ink-soft:#8a8d99;
  --line:#b9bccb;
  --nav:#373a49;
  --nav-active:#5b5e6d;
  --nav-text:#c9cbd3;
  --chip:#8e909c;
}
*{box-sizing:border-box;margin:0;padding:0}
html,body{width:1200px;height:900px;overflow:hidden}
body{background:radial-gradient(ellipse at center,#f6f7f7 0%,var(--page) 75%);font-family:"Arimo",Arial,sans-serif;position:relative}
.app{position:absolute;left:100px;top:120px;width:1000px;height:660px;background:var(--white);box-shadow:0 10px 40px rgba(0,0,0,.28)}
.header{position:absolute;left:0;top:0;width:1000px;height:60px;background:linear-gradient(var(--header-top),var(--header-bottom))}
.brand{position:absolute;left:0;top:0;width:200px;height:60px;border-right:1px solid rgba(255,255,255,.35);display:flex;align-items:center;padding-left:20px;gap:10px}
.brand-mark{width:34px;height:34px;border-radius:50%;background:var(--white);opacity:.9}
.brand-name{color:var(--white);font-weight:700;font-size:18px;line-height:18px}
.brand-slogan{color:var(--white);font-size:9px;margin-top:2px}
.welcome{position:absolute;left:215px;top:21px;color:#e8f5fd;font-size:15px}
.welcome b{color:var(--white)}
.text-size{position:absolute;left:610px;top:17px;color:var(--white);display:flex;align-items:baseline;gap:12px;font-family:"Arimo",sans-serif}
.text-size span:nth-child(1){font-size:11px;opacity:.85}
.text-size span:nth-child(2){font-size:16px;font-weight:700}
.text-size span:nth-child(3){font-size:20px;opacity:.9}
.search{position:absolute;left:686px;top:14px;width:163px;height:31px;border:1px solid rgba(255,255,255,.45);background:rgba(40,120,190,.25);color:#d5ecfb;font-size:14px;padding:8px 9px}
.search svg{position:absolute;right:8px;top:7px}
.btn{position:absolute;top:14px;height:31px;background:linear-gradient(#54aee5,#3785c8);border:1px solid rgba(255,255,255,.35);box-shadow:0 1px 2px rgba(0,40,90,.4);color:var(--white);font-weight:700;font-size:16px;text-align:center;line-height:29px}
.btn-help{left:888px;width:32px}
.btn-exit{left:934px;width:52px}
.subheader{position:absolute;left:0;top:60px;width:1000px;height:70px;background:var(--panel);border-bottom:1px solid #e4e4e7}
.section-title{position:absolute;left:16px;top:26px;color:var(--accent);font-weight:700;font-size:17px}
.subheader .divider{position:absolute;left:199px;top:0;width:1px;height:70px;background:#e0e0e3}
.add{position:absolute;left:230px;top:23px;display:flex;align-items:center;gap:7px;color:var(--ink-soft);font-weight:700;font-size:15px}
.settings{position:absolute;left:944px;top:22px}
.sidebar{position:absolute;left:0;top:130px;width:200px;height:400px;background:var(--panel);border-right:1px solid #e0e0e3}
.tab{position:absolute;left:10px;width:190px;height:90px;display:flex;align-items:center;gap:14px;padding-left:30px;font-weight:700;font-size:15px;color:var(--ink-soft)}
.tab.active{background:var(--white);color:var(--ink);box-shadow:0 2px 4px rgba(0,0,0,.12)}
.tab-sugar{top:0}
.tab-pressure{top:100px}
.records{position:absolute;left:229px;top:160px;width:742px}
.record{position:relative;height:62px;border:1px solid var(--line);border-radius:3px;background:var(--white);margin-bottom:30px;display:flex;align-items:center;font-size:15px}
.record .date{position:absolute;left:14px;color:var(--ink);font-weight:700}
.record .note{position:absolute;left:148px;color:#6a6d7a}
.record .chip{position:absolute;left:148px;background:var(--chip);color:var(--white);font-weight:700;font-size:13px;padding:7px 7px;border-radius:2px}
.record .value{position:absolute;left:577px;color:var(--accent);font-weight:700}
.record .info{position:absolute;left:700px}
.nav{position:absolute;left:0;top:530px;width:1000px;height:130px;background:var(--nav);display:flex}
.nav-item{flex:1;border-right:1px solid #2f3240;display:flex;flex-direction:column;align-items:center;color:var(--nav-text);font-weight:700;font-size:14px;text-align:center;line-height:17px;padding-top:30px}
.nav-item:last-child{border-right:0}
.nav-item svg{height:34px;margin-bottom:12px}
.nav-item.active{background:var(--nav-active);color:var(--white);border-left:2px solid #2c2f3c}
.nav-item.two-line svg{margin-bottom:6px}
</style>
</head>
<body>
<div class="app">
  <header class="header">
    <div class="brand">
      <div class="brand-mark"></div>
      <div><div class="brand-name">AppName</div><div class="brand-slogan">Here is your slogan</div></div>
    </div>
    <p class="welcome">Welcome back, <b>Walter Grey</b></p>
    <div class="text-size"><span>A</span><span>A</span><span>A</span></div>
    <div class="search">Search
      <svg width="16" height="16" viewBox="0 0 16 16"><circle cx="6.5" cy="6.5" r="4.8" fill="none" stroke="#fff" stroke-width="2"/><line x1="10" y1="10" x2="14.5" y2="14.5" stroke="#fff" stroke-width="2.4" stroke-linecap="round"/></svg>
    </div>
    <div class="btn btn-help">?</div>
    <div class="btn btn-exit">Exit</div>
  </header>

  <div class="subheader">
    <h1 class="section-title">Home Measurements</h1>
    <div class="divider"></div>
    <div class="add">
      <svg width="26" height="26" viewBox="0 0 26 26"><circle cx="13" cy="13" r="11.5" fill="none" stroke="#8a8d99" stroke-width="2"/><path d="M13 7v12M7 13h12" stroke="#8a8d99" stroke-width="2.6"/></svg>
      Add measurement
    </div>
    <svg class="settings" width="27" height="27" viewBox="0 0 27 27"><circle cx="13.5" cy="13.5" r="12" fill="none" stroke="#8a8d99" stroke-width="2"/><circle cx="13.5" cy="13.5" r="5" fill="none" stroke="#8a8d99" stroke-width="3.5" stroke-dasharray="2.6 1.3"/><circle cx="13.5" cy="13.5" r="2" fill="#8a8d99"/></svg>
  </div>

  <aside class="sidebar">
    <div class="tab tab-sugar active">
      <svg width="22" height="34" viewBox="0 0 22 34"><path d="M11 1C8 10 1 16 1 23a10 10 0 0 0 20 0C21 16 14 10 11 1z" fill="#5d6070"/><path d="M6 24a5 5 0 0 0 5 5" stroke="#fff" stroke-width="1.6" fill="none"/></svg>
      Sugar Level
    </div>
    <div class="tab tab-pressure">
      <svg width="34" height="34" viewBox="0 0 34 34"><circle cx="17" cy="17" r="15" fill="none" stroke="#8a8d99" stroke-width="3"/><path d="M17 19l6-7" stroke="#8a8d99" stroke-width="3" stroke-linecap="round"/><circle cx="17" cy="19" r="2.4" fill="#8a8d99"/></svg>
      Pressure
    </div>
  </aside>

  <main class="records">
    <div class="record">
      <span class="date">01/01/2013</span>
      <span class="note">My Sugar Level</span>
      <span class="value">6,3 mmol/l</span>
      <svg class="info" width="20" height="20" viewBox="0 0 20 20"><circle cx="10" cy="10" r="9" fill="none" stroke="#a4a7b3" stroke-width="1.2"/><text x="10" y="15" text-anchor="middle" font-family="Georgia,serif" font-style="italic" font-size="13" fill="#a4a7b3">i</text></svg>
    </div>
    <div class="record">
      <span class="date">02/21/2013</span>
      <span class="chip">Add comment</span>
      <span class="value">7,9 mmol/l</span>
      <svg class="info" width="20" height="20" viewBox="0 0 20 20"><circle cx="10" cy="10" r="9" fill="none" stroke="#a4a7b3" stroke-width="1.2"/><text x="10" y="15" text-anchor="middle" font-family="Georgia,serif" font-style="italic" font-size="13" fill="#a4a7b3">i</text></svg>
    </div>
  </main>

  <nav class="nav">
    <div class="nav-item">
      <svg width="34" height="34" viewBox="0 0 34 34"><rect x="4" y="2" width="10" height="22" rx="5" transform="rotate(-25 9 13)" fill="none" stroke="#c9cbd3" stroke-width="2"/><rect x="15" y="14" width="16" height="10" rx="5" transform="rotate(40 23 19)" fill="#c9cbd3"/></svg>
      Medications
    </div>
    <div class="nav-item active two-line">
      <svg width="34" height="34" viewBox="0 0 34 34"><path d="M25 3a3.5 3.5 0 0 1 5 5L13 25a5 5 0 1 1-5-5z" fill="none" stroke="#fff" stroke-width="2"/><circle cx="10" cy="24" r="2.5" fill="#fff"/><path d="M17 14l2 2M20 11l2 2M23 8l2 2" stroke="#fff" stroke-width="1.5"/></svg>
      Home<br>Measurements
    </div>
    <div class="nav-item">
      <svg width="34" height="34" viewBox="0 0 34 34"><rect x="2" y="5" width="30" height="27" fill="none" stroke="#c9cbd3" stroke-width="2"/><rect x="2" y="5" width="30" height="6" fill="#c9cbd3"/><path d="M9 2v6M25 2v6" stroke="#c9cbd3" stroke-width="3"/><text x="17" y="27" text-anchor="middle" font-family="Arimo,sans-serif" font-size="12" fill="#c9cbd3">17</text></svg>
      My Schedule
    </div>
    <div class="nav-item">
      <svg width="34" height="34" viewBox="0 0 34 34"><rect x="2" y="2" width="30" height="22" fill="none" stroke="#c9cbd3" stroke-width="2"/><path d="M5 14h6l2-6 4 11 3-8 2 3h7" fill="none" stroke="#c9cbd3" stroke-width="1.6"/><path d="M12 24l-4 8M22 24l4 8" stroke="#c9cbd3" stroke-width="2"/></svg>
      Lab Test Results
    </div>
    <div class="nav-item two-line">
      <svg width="34" height="34" viewBox="0 0 34 34"><g fill="none" stroke="#c9cbd3" stroke-width="2"><rect x="2" y="3" width="6" height="6"/><rect x="2" y="14" width="6" height="6"/><rect x="2" y="25" width="6" height="6"/></g><g fill="#c9cbd3"><rect x="12" y="4" width="20" height="4"/><rect x="12" y="15" width="20" height="4"/><rect x="12" y="26" width="20" height="4"/></g></svg>
      Checkups &amp;<br>Procedures
    </div>
    <div class="nav-item">
      <svg width="34" height="34" viewBox="0 0 34 34"><circle cx="17" cy="10" r="7.5" fill="#c9cbd3"/><path d="M2 33c0-9 6-13 15-13s15 4 15 13z" fill="#c9cbd3"/></svg>
      My Profile
    </div>
    <div class="nav-item two-line">
      <svg width="34" height="34" viewBox="0 0 34 34"><path d="M17 31L4 18A8 8 0 0 1 17 7a8 8 0 0 1 13 11z" fill="#c9cbd3"/></svg>
      My Health Care<br>Providers
    </div>
  </nav>
</div>
</body>
</html>
```